The Copper Kite Website Redesign

I want a new design and website for www.thecopperkitebrookvale.com where part of the home page includes our daily specials from our POS Toast to be pulled from API. I have included photos and links to give you a better feel for the style of our restaurant.

Coding

Coded - Design and coding required

```html
<!DOCTYPE html>
<html lang="en">
<head>
<meta charset="utf-8">
<title>The Copper Kite – A Finer Diner</title>
<link rel="stylesheet" href="https://fonts.googleapis.com/css2?family=Caveat:wght@600;700&family=Lato:wght@400;700&display=swap">
<style>
:root{
  --orange:#ff7a00;
  --red:#e8191b;
  --ink:#1a1a1a;
  --hero-dark:#1f252d;
  --grey-text:#555;
  --white:#fff;
  --footer:#121212;
  --script:'Caveat',cursive;
  --sans:'Lato',sans-serif;
}
*{box-sizing:border-box;margin:0;padding:0}
html,body{width:1200px;height:2525px;overflow:hidden}
body{position:relative;background:var(--white);font-family:var(--sans);color:var(--ink)}
.btn{position:absolute;display:flex;align-items:center;justify-content:center;border-radius:24px;color:var(--white);font-family:var(--sans);font-weight:700;font-size:16px}
.btn-orange{background:var(--orange)}
.btn-red{background:var(--red)}

/* hero */
.hero{position:absolute;left:0;top:0;width:1200px;height:557px;background:radial-gradient(circle at 20% 40%,#2b323c,var(--hero-dark) 70%);overflow:hidden}
.hero-photo{position:absolute;left:470px;top:0;width:730px;height:557px;background:radial-gradient(ellipse at 60% 35%,#d94a1c 0%,#b8741e 30%,#5a3a22 60%,rgba(31,37,45,0) 78%)}
.brand{position:absolute;left:86px;top:52px;display:flex;align-items:center;gap:10px;color:var(--white);font-family:var(--sans);font-weight:700;font-size:26px;line-height:1}
.brand-mark{width:12px;height:12px;border-radius:50%;background:var(--white)}
.menu-pill{position:absolute;left:972px;top:28px;width:118px;height:42px;border-radius:21px;background:var(--white);display:flex;align-items:center;justify-content:center;gap:12px;color:var(--red);font-size:15px}
.hero-title{position:absolute;left:82px;top:198px;color:var(--white);font-family:var(--script);font-weight:700;font-size:66px;line-height:70px}
.hero-text{position:absolute;left:82px;top:355px;width:380px;color:var(--white);font-size:16px;line-height:28px}
.notch{position:absolute;left:530px;top:515px}

/* about */
.dots{position:absolute;background:#eeeeee}
.about-photo{position:absolute;left:112px;top:662px;width:488px;height:352px;border-radius:30px;background:linear-gradient(90deg,#2a2a2e 0 18%,#d9cf2c 18% 100%);box-shadow:0 20px 40px rgba(0,0,0,.15)}
.section-title{position:absolute;font-family:var(--script);font-weight:700;color:var(--ink);text-align:center}
.about-text{position:absolute;left:676px;top:748px;width:386px;text-align:center;font-size:15px;line-height:31px;color:var(--grey-text)}

/* menu */
.menu-photo{position:absolute;left:0;top:1123px;width:452px;height:612px;background:radial-gradient(circle at 45% 50%,#c47a2c 0%,#6a3a1c 35%,#161616 70%)}
.menu-panel{position:absolute;left:452px;top:1123px;width:748px;height:612px;background:var(--orange)}
.menu-frame{position:absolute;left:490px;top:1165px;width:672px;height:528px;border:2px solid var(--red)}
.tab{position:absolute;height:60px;border-radius:30px 0 0 30px;display:flex;align-items:center;padding-left:34px;font-family:var(--script);font-weight:700;font-size:28px}
.tab-active{left:286px;width:204px;background:var(--red);color:var(--white)}
.tab-idle{left:248px;width:204px;background:var(--white);color:#7a7a7a}
.menu-head{position:absolute;left:525px;top:1195px;color:var(--white);font-family:var(--script);font-weight:700;font-size:34px}
.menu-sub{position:absolute;left:525px;top:1242px;color:var(--white);font-size:16px}
.menu-rule{position:absolute;left:525px;top:1285px;width:602px;height:1px;background:rgba(255,255,255,.6)}
.dish{position:absolute;left:525px;width:602px;color:var(--white)}
.dish-name{font-size:18px;font-weight:700;line-height:24px}
.dish-desc{font-size:13.5px;line-height:20px;margin-top:4px;width:500px}
.dish-price{position:absolute;right:0;top:12px;font-size:24px;font-weight:700}

/* specials */
.specials-sub{position:absolute;left:0;top:1890px;width:1200px;text-align:center;font-size:17px;color:var(--grey-text)}
.card{position:absolute;top:1937px;width:312px;height:412px;border-radius:14px;background:var(--white);box-shadow:0 4px 24px rgba(0,0,0,.08)}
.card-photo{position:absolute;left:5px;top:5px;width:302px;height:222px}
.card-name{position:absolute;left:27px;top:250px;font-family:var(--script);font-weight:700;font-size:26px}
.card-price{position:absolute;right:28px;top:254px;color:var(--red);font-weight:700;font-size:21px}
.card-text{position:absolute;left:20px;top:300px;width:272px;text-align:center;font-size:14px;line-height:21px;color:var(--grey-text)}
.card .buy{left:27px;top:353px;width:202px;height:40px;font-size:15px}
.cart{position:absolute;left:244px;top:353px;width:40px;height:40px;border-radius:50%;background:var(--red);display:flex;align-items:center;justify-content:center}
.pager{position:absolute;top:2378px;width:28px;height:28px;border-radius:50%;display:flex;align-items:center;justify-content:center}

/* footer */
.footer{position:absolute;left:0;top:2463px;width:1200px;height:62px;background:var(--footer)}
.copyright{position:absolute;left:110px;top:22px;color:var(--white);font-size:13px}
.social{position:absolute;top:15px;width:32px;height:32px;border-radius:50%;background:var(--white)}
</style>
</head>
<body>

<header class="hero">
  <div class="hero-photo" role="img" aria-label="Bowl of stir-fried noodles with peppers, mushrooms and chopsticks"></div>
  <div class="brand"><span class="brand-mark"></span><span>The Copper Kite</span></div>
  <div class="menu-pill">
    <svg width="16" height="12" viewBox="0 0 16 12"><rect y="0" width="16" height="2" fill="#e8191b"/><rect y="5" width="12" height="2" fill="#e8191b"/><rect y="10" width="16" height="2" fill="#e8191b"/></svg>
    <span>Menu</span>
  </div>
  <h1 class="hero-title">Savor the Flavor<br>of Every Bite</h1>
  <p class="hero-text">Perspiciatis unde omnis iste natus error sit volup tatem accusantium doloremque</p>
  <div class="btn btn-orange" style="left:82px;top:426px;width:140px;height:42px">Get Started</div>
  <svg class="notch" width="140" height="42" viewBox="0 0 140 42">
    <path d="M0 42 C30 42 40 0 70 0 C100 0 110 42 140 42 Z" fill="#fff"/>
    <rect x="59" y="18" width="22" height="34" rx="11" fill="#9a9a9a"/>
    <path d="M70 24 V38 M65 33 L70 38 L75 33" stroke="#fff" stroke-width="1.6" fill="none"/>
  </svg>
</header>

<section class="about">
  <div class="dots" role="img" aria-label="Dotted accent" style="left:70px;top:622px;width:140px;height:140px;opacity:.7"></div>
  <div class="dots" role="img" aria-label="Dotted accent" style="left:495px;top:900px;width:140px;height:140px;opacity:.7"></div>
  <div class="about-photo" role="img" aria-label="Diner storefront with yellow brick wall and awning"></div>
  <h2 class="section-title" style="left:676px;top:670px;width:386px;font-size:60px">About Us</h2>
  <p class="about-text">The doors of the Copper Kite: A finer diner were eagerly thrown open for the first time on December 28th 2004. We welcomed our first customer and started our magnificent life as a business that continues on through today. Along with our beloved and inquisitive customers came the many questions of our origin.</p>
  <div class="btn btn-orange" style="left:800px;top:952px;width:139px;height:42px">Read More</div>
</section>

<section class="menu">
  <div class="menu-photo" role="img" aria-label="Cheeseburger with sesame bun on dark background"></div>
  <div class="menu-panel"></div>
  <div class="menu-frame"></div>
  <div class="tab tab-active" style="top:1268px">All Things Eggs</div>
  <div class="tab tab-idle" style="top:1356px">Green Things</div>
  <div class="tab tab-idle" style="top:1444px">Between Bread</div>
  <div class="tab tab-idle" style="top:1532px">Other Stuff</div>

  <h3 class="menu-head">All Things Eggs</h3>
  <p class="menu-sub">Comes With Toast &amp; Smashed Garlic Fried Potatoes when Logical</p>
  <div class="btn btn-red" style="left:1013px;top:1210px;width:114px;height:42px;font-size:15px">View More</div>
  <div class="menu-rule"></div>

  <div class="dish" style="top:1305px"><div class="dish-name">Green Eggs and Ham</div><div class="dish-desc">Poblano Pesto and Jack Cheese Rumbled with Eggs Sidled by Seared City Ham</div><div class="dish-price">$13.95</div></div>
  <div class="dish" style="top:1379px"><div class="dish-name">Veggie Rumble</div><div class="dish-desc" style="width:540px">Red Pepper, Carrots, Mushrooms, Peas, Spinach and Provolone. Choose Eggs or Tofu</div><div class="dish-price">$12.95</div></div>
  <div class="dish" style="top:1450px"><div class="dish-name">The Boot</div><div class="dish-desc">Marco's Fave - a Rumble of Eggs with Fresh Mozzarella, Basil, Tomatoes, &amp; Green Olives</div><div class="dish-price">$12.95</div></div>
  <div class="dish" style="top:1542px"><div class="dish-name">The Forager</div><div class="dish-desc">Mushrooms, Caramelized Onion, Smoked Gouda &amp; Greens Rumbled with Eggs</div><div class="dish-price">$13.95</div></div>
  <div class="dish" style="top:1613px"><div class="dish-name">Red Flannel Hash</div><div class="dish-desc">Hot Spiced Beef Brisket, Potatoes, Beets &amp; Onion with Two Eggs and Scallions</div><div class="dish-price">$13.95</div></div>
</section>

<section class="specials">
  <h2 class="section-title" style="left:0;top:1800px;width:1200px;font-size:64px">Our Daily Specials</h2>
  <p class="specials-sub">Sed ut perspiciatis unde omnis iste natus error sit voluptatem accusantium doloremque laudant</p>

  <article class="card" style="left:109px">
    <div class="card-photo" role="img" aria-label="Burritos on a plate" style="background:linear-gradient(160deg,#6b3b22,#c9a57e 55%,#3a2a26)"></div>
    <div class="card-name">Burrito</div><div class="card-price">$14.95</div>
    <p class="card-text">Sed ut perspiciatis unde omnis iste nat us error sit voluptatem accusantium</p>
    <div class="btn btn-orange buy">Buy Now</div>
    <div class="cart"><svg width="14" height="12" viewBox="0 0 14 12"><path d="M0 1H3L4.5 8H12L13.5 3H4" fill="none" stroke="#fff" stroke-width="1.6"/><circle cx="5" cy="10.5" r="1.2" fill="#fff"/><circle cx="11" cy="10.5" r="1.2" fill="#fff"/></svg></div>
  </article>
  <article class="card" style="left:444px">
    <div class="card-photo" role="img" aria-label="Gingerbread waffles and cookies on grey cloth" style="background:linear-gradient(160deg,#8d8a86,#b08552 50%,#6f6c69)"></div>
    <div class="card-name">Gingerbread Waffle</div><div class="card-price">$10.95</div>
    <p class="card-text">Sed ut perspiciatis unde omnis iste nat us error sit voluptatem accusantium</p>
    <div class="btn btn-orange buy">Buy Now</div>
    <div class="cart"><svg width="14" height="12" viewBox="0 0 14 12"><path d="M0 1H3L4.5 8H12L13.5 3H4" fill="none" stroke="#fff" stroke-width="1.6"/><circle cx="5" cy="10.5" r="1.2" fill="#fff"/><circle cx="11" cy="10.5" r="1.2" fill="#fff"/></svg></div>
  </article>
  <article class="card" style="left:779px">
    <div class="card-photo" role="img" aria-label="Tray of mini muffins" style="background:linear-gradient(160deg,#c9985a,#e2c9a0 50%,#a87a44)"></div>
    <div class="card-name">Mini-Muffin</div><div class="card-price">$14.95</div>
    <p class="card-text">Sed ut perspiciatis unde omnis iste nat us error sit voluptatem accusantium</p>
    <div class="btn btn-orange buy">Buy Now</div>
    <div class="cart"><svg width="14" height="12" viewBox="0 0 14 12"><path d="M0 1H3L4.5 8H12L13.5 3H4" fill="none" stroke="#fff" stroke-width="1.6"/><circle cx="5" cy="10.5" r="1.2" fill="#fff"/><circle cx="11" cy="10.5" r="1.2" fill="#fff"/></svg></div>
  </article>

  <div class="pager" style="left:568px;background:#fbd3d3"><svg width="10" height="8" viewBox="0 0 10 8"><path d="M5 1L2 4L5 7M9 1L6 4L9 7" fill="none" stroke="#e8191b" stroke-width="1.4"/></svg></div>
  <div class="pager" style="left:604px;background:var(--red)"><svg width="10" height="8" viewBox="0 0 10 8"><path d="M1 1L4 4L1 7M5 1L8 4L5 7" fill="none" stroke="#fff" stroke-width="1.4"/></svg></div>
</section>

<footer class="footer">
  <p class="copyright">(C) Copyright 2025 | All Rights Reserved</p>
  <div class="social" style="left:940px" aria-label="Social link"></div>
  <div class="social" style="left:979px" aria-label="Social link"></div>
  <div class="social" style="left:1018px" aria-label="Social link"></div>
  <div class="social" style="left:1057px" aria-label="Social link"></div>
</footer>

</body>
</html>
```